New Webpage for High Class Expert Witness Services Company

We are looking for a minimalist design for a webpage that just has our logo and an entry form offer to connect with one of our Liaisons.
The entry form should just ask for Name, Email, Contact Info and Description of Project.

Company Name is: The Marlowe Crest Advisory Services

Number of Pages Required

1 page

```html
<!DOCTYPE html>
<html lang="en">
<head>
<meta charset="UTF-8">
<title>The Marlowe Crest Advisory Services — Connect</title>
<link rel="stylesheet" href="https://fonts.googleapis.com/css2?family=Poppins:wght@400;600;700&display=swap">
<style>
  :root {
    --bg: #131313;
    --card: #ffffff;
    --field: #ececec;
    --placeholder: #a9a9a9;
    --icon: #9a9a9a;
    --ink: #111111;
    --white: #ffffff;
    --brand: #d9d9d9;
  }
  * { box-sizing: border-box; margin: 0; padding: 0; }
  html, body { width: 1200px; height: 788px; overflow: hidden; }
  body {
    position: relative;
    background: var(--bg);
    font-family: "Poppins", sans-serif;
    color: var(--ink);
  }
  .backdrop-scene {
    position: absolute; inset: 0;
    background:
      radial-gradient(ellipse 260px 300px at 230px 560px, #333 0%, rgba(40,40,40,0.5) 55%, transparent 100%),
      radial-gradient(ellipse 320px 360px at 1130px 560px, #2a2a2a 0%, rgba(35,35,35,0.4) 60%, transparent 100%),
      linear-gradient(180deg, var(--bg) 0%, var(--bg) 38%, #1b1b1b 70%, #171717 100%);
  }
  .brand {
    position: absolute; left: 0; right: 0; top: 91px; height: 28px;
    display: flex; align-items: center; justify-content: center; gap: 12px;
  }
  .brand-mark { width: 28px; height: 28px; background: var(--brand); }
  .brand-name {
    font-weight: 600; font-size: 17px; line-height: 1; letter-spacing: 1px;
    color: var(--brand); text-transform: uppercase;
  }
  .contact-card {
    position: absolute; left: 388px; top: 189px;
    width: 424px; height: 452px;
    background: var(--card); border-radius: 22px;
  }
  .field-label {
    position: absolute; left: 37px;
    font-size: 10px; line-height: 1; font-weight: 600; text-transform: uppercase;
  }
  .field {
    position: absolute; left: 38px; width: 348px; height: 40px;
    background: var(--field); border-radius: 7px;
    display: flex; align-items: center; justify-content: space-between;
    padding: 0 16px;
    font-size: 11px; line-height: 1; color: var(--placeholder);
  }
  .field svg { width: 11px; height: 11px; fill: var(--icon); }
  .field-area { height: 85px; align-items: flex-start; padding-top: 14px; }
  .submit-button {
    position: absolute; left: 38px; top: 371px; width: 348px; height: 43px;
    background: var(--ink); color: var(--white); border: 0; border-radius: 7px;
    display: flex; align-items: center; justify-content: center;
    font-family: inherit; font-size: 10.5px; line-height: 1; font-weight: 600; text-transform: uppercase;
  }
  .submit-button svg { position: absolute; right: 15px; width: 12px; height: 12px; fill: var(--white); }
  .copyright {
    position: absolute; left: 0; right: 0; top: 745px;
    text-align: center; color: var(--white);
    font-size: 10.5px; line-height: 1; font-weight: 600; text-transform: uppercase;
  }
</style>
</head>
<body>
  <div class="backdrop-scene" role="img" aria-label="Dim monochrome backdrop of a soldier in tactical gear on the left and a glowing globe with network lines on the right"></div>

  <header class="brand">
    <span class="brand-mark"></span>
    <span class="brand-name">The Marlowe Crest Advisory Services</span>
  </header>

  <form class="contact-card">
    <span class="field-label" style="top:29px">Name</span>
    <div class="field" style="top:45px">
      <span>Johny</span>
      <svg viewBox="0 0 12 12"><circle cx="6" cy="3.2" r="2.6"/><path d="M1 12c0-3 2.2-5 5-5s5 2 5 5z"/></svg>
    </div>

    <span class="field-label" style="top:101px">Email</span>
    <div class="field" style="top:117px">
      <span>Johny@example.com</span>
      <svg viewBox="0 0 12 12"><path d="M0 2.5h12v1L6 7 0 3.5z"/><path d="M0 4.8l6 3.4 6-3.4V10H0z"/></svg>
    </div>

    <span class="field-label" style="top:174px">Contact Info</span>
    <div class="field" style="top:190px">
      <span>+081 123456 789</span>
      <svg viewBox="0 0 12 12"><path d="M2.5 0.5l2 2.4-1.1 1.6c.8 1.7 2.1 3 3.9 3.9l1.6-1.1 2.4 2-1 2.2C4.8 11.5 0.4 7.1 0.3 1.5z"/></svg>
    </div>

    <span class="field-label" style="top:247px">Description of Project</span>
    <div class="field field-area" style="top:263px">
      <span></span>
      <svg viewBox="0 0 12 12"><ellipse cx="7" cy="4.5" rx="4.8" ry="4"/><ellipse cx="3.5" cy="7" rx="3" ry="2.6"/><path d="M1.5 9l-1 2.5 3-1.3z"/></svg>
    </div>

    <button type="button" class="submit-button">
      Connect with us
      <svg viewBox="0 0 12 12"><path d="M12 0L0 5l3.5 1.6L10 2 4.5 7.5V12l2.3-3 3 1.5z"/></svg>
    </button>
  </form>

  <footer class="copyright">© Copyright 2026</footer>
</body>
</html>
```